Business card design Needed for new logo / Construction business, home extensions and new builds

We need a business card design using our new logo files which i will attach to this project :)

We are a small construction business specialising in home extensions, new builds and property development. We are very ambitious and would appreciate professional and elegant designs for our new business card.

Very serious about using the services on MakerQuarry and recently acquired our new logo from here :)

Please get involved, i will feedback when i can as i am very busy but can respond daily, thanks

Target Market(s)

People that want to build onto their houses, new building developments or adding too their existing property

Industry/Entity Type

Construction

Contact Information for Business Card

Renwick Tolliver Construction, Lionel Ashby (Managing Director), Tel 07822254961, email - info@renwick-tolliver, www.renwick-tolliver.co.uk

Colors

Designer to choose colors to be used in the design.

Requirements
Must have
• I like a deep grey on the back please. A lot of you have provided black from and back, try mixing things up a little. The black looks cool 😎 Thanks

```html
<!DOCTYPE html>
<html lang="en">
<head>
<meta charset="utf-8">
<title>Renwick Tolliver Construction – Business Card</title>
<link rel="stylesheet" href="https://fonts.googleapis.com/css2?family=Montserrat:wght@400;500;700&display=swap">
<style>
  :root {
    --stage: #2e2e30;
    --card-front: #3a3a3f;
    --card-back: #1e1e1f;
    --panel: #ffffff;
    --gold: #d9a430;
    --text-light: #f2f2f2;
  }
  * { box-sizing: border-box; margin: 0; padding: 0; }
  html, body {
    width: 1200px; height: 689px; overflow: hidden;
    background: var(--stage);
    font-family: "Montserrat", Arial, sans-serif;
  }
  .canvas {
    position: relative; width: 1200px; height: 689px;
    display: flex; align-items: center; justify-content: center; gap: 60px;
  }
  .card {
    position: relative; width: 525px; height: 300px;
    border-radius: 16px; overflow: hidden;
    box-shadow: 0 14px 30px rgba(0,0,0,.45);
  }

  .brand { display: flex; align-items: center; gap: 14px; }
  .brand__mark { width: 22px; height: 22px; background: var(--gold); flex: none; }
  .brand__name {
    color: var(--gold); font-weight: 500; font-size: 24px;
    letter-spacing: 2px; text-transform: uppercase; line-height: 1.35;
  }

  /* Front */
  .card--front {
    background: var(--card-front);
    display: flex; align-items: center; justify-content: center;
  }

  /* Back */
  .card--back { background: var(--card-back); }
  .card__panel { position: absolute; inset: 0; }
  .card__brand {
    position: absolute; right: 22px; top: 50%; transform: translateY(-50%);
    width: 180px; gap: 10px;
  }
  .card__brand .brand__name { font-size: 14px; letter-spacing: 1.5px; }
  .card__brand .brand__mark { width: 14px; height: 14px; }

  .contact { position: absolute; left: 40px; top: 54px; color: var(--text-light); }
  .contact__mark { width: 26px; height: 26px; background: var(--gold); margin-bottom: 22px; }
  .contact__name {
    color: var(--gold); font-weight: 700; font-size: 24px;
    letter-spacing: .5px; text-transform: uppercase; line-height: 1.2;
  }
  .contact__role { font-size: 15px; margin-bottom: 16px; }
  .contact__list { list-style: none; font-size: 14px; line-height: 1.6; margin-bottom: 14px; }
  .contact__list li { display: flex; align-items: center; gap: 9px; }
  .contact__list svg { width: 12px; height: 12px; fill: var(--gold); flex: none; }
  .contact__address { font-size: 14px; line-height: 1.5; }
</style>
</head>
<body>
<main class="canvas">

  <section class="card card--front" aria-label="Card front">
    <div class="brand">
      <span class="brand__mark"></span>
      <span class="brand__name">Renwick Tolliver<br>Construction</span>
    </div>
  </section>

  <section class="card card--back" aria-label="Card back">
    <svg class="card__panel" viewBox="0 0 525 300" preserveAspectRatio="none" aria-hidden="true">
      <path d="M330 0 C300 110 320 240 450 300 L525 300 L525 0 Z" fill="var(--panel)"/>
    </svg>

    <div class="card__brand brand">
      <span class="brand__mark"></span>
      <span class="brand__name">Renwick<br>Tolliver<br>Construction</span>
    </div>

    <div class="contact">
      <div class="contact__mark"></div>
      <p class="contact__name">Lionel Ashby</p>
      <p class="contact__role">Managing Director</p>
      <ul class="contact__list">
        <li><svg viewBox="0 0 24 24"><path d="M6.6 10.8a15 15 0 0 0 6.6 6.6l2.2-2.2a1 1 0 0 1 1-.25 11.4 11.4 0 0 0 3.6.57 1 1 0 0 1 1 1V20a1 1 0 0 1-1 1A17 17 0 0 1 3 4a1 1 0 0 1 1-1h3.5a1 1 0 0 1 1 1c0 1.25.2 2.45.57 3.57a1 1 0 0 1-.25 1z"/></svg>123 456 789</li>
        <li><svg viewBox="0 0 24 24"><path d="M2 5h20v14H2z M3 6.5v1l9 6.5 9-6.5v-1l-9 6.5z" fill-rule="evenodd"/></svg>info@yourmail.com</li>
        <li><svg viewBox="0 0 24 24"><circle cx="12" cy="12" r="10"/></svg>www.yourwebsite.com</li>
      </ul>
      <p class="contact__address">Your address, City<br>State, Zip 1234</p>
    </div>
  </section>

</main>
</body>
</html>
```